A clean crisp business card for a Landscape Construction company. Designed to be easy to read contact/ info and also be appealing/interesting, unlike a traditional business card.

Industry/Entity Type

Landscape Construction

Contact Information for Business Card

Company name : Brambleford Landscape Construction, phone number: (877) 62Vista, website:Bramblefordyards.example, Email, sales@bramblefordyards.example

Requirements
Nice to have
• Luxurious finishes/ details…. Icons or emblems next to contact info
Should not have
• Clipart or general pictures

```html
<!DOCTYPE html>
<html lang="en">
<head>
<meta charset="utf-8">
<title>Brambleford Landscape Construction – Business Card</title>
<link href="https://fonts.googleapis.com/css2?family=Cinzel:wght@400;600&family=Arimo:wght@400&display=swap" rel="stylesheet">
<style>
  :root {
    --backdrop: #3a3230;
    --card-black: #141414;
    --brand-blue: #2a78d3;
    --brand-green: #a6d63a;
    --ink-white: #ffffff;
  }
  * { box-sizing: border-box; margin: 0; padding: 0; }
  html, body { width: 1200px; height: 716px; overflow: hidden; }
  body {
    background: var(--backdrop);
    position: relative;
    font-family: "Arimo", Arial, sans-serif;
  }
  .card {
    position: absolute;
    top: 208px;
    width: 525px;
    height: 300px;
    border: 2px solid var(--brand-green);
    border-radius: 3px;
    overflow: hidden;
    box-shadow: 0 14px 30px rgba(0,0,0,.45);
  }
  .card--front { left: 50px; background: var(--card-black); }
  .card--back { left: 625px; background: var(--card-black); }

  .brand {
    position: absolute;
    display: flex;
    align-items: center;
    gap: 12px;
    color: var(--brand-green);
    font-family: "Cinzel", "Times New Roman", serif;
    font-weight: 600;
  }
  .brand__dot {
    width: 22px; height: 22px;
    border-radius: 50%;
    background: var(--brand-blue);
    flex: none;
  }
  .brand__name { line-height: 1.15; }
  .brand__title { display: block; font-size: 30px; letter-spacing: 1px; }
  .brand__sub { display: block; font-size: 11.5px; letter-spacing: 2.6px; }

  .card--front .brand { left: 50%; top: 50%; transform: translate(-50%, -50%); }
  .card--back .brand { left: 40px; top: 38px; }
  .card--back .brand__title { font-size: 26px; }
  .card--back .brand__sub { font-size: 10px; letter-spacing: 2.2px; }

  .waves { position: absolute; inset: 0; width: 100%; height: 100%; }

  .contact {
    position: absolute;
    right: 26px;
    bottom: 16px;
    text-align: right;
    color: var(--ink-white);
  }
  .contact__name {
    font-family: "Cinzel", "Times New Roman", serif;
    font-size: 18px;
    letter-spacing: 1px;
    line-height: 1.2;
  }
  .contact__role {
    font-family: "Cinzel", "Times New Roman", serif;
    font-size: 12px;
    letter-spacing: 1.5px;
    margin-bottom: 6px;
  }
  .contact__line {
    display: flex;
    justify-content: flex-end;
    align-items: center;
    gap: 6px;
    font-size: 12px;
    line-height: 1.45;
  }
  .contact__icon { width: 11px; height: 11px; flex: none; }
</style>
</head>
<body>

  <section class="card card--front" aria-label="Business card front">
    <div class="brand">
      <span class="brand__dot"></span>
      <span class="brand__name">
        <span class="brand__title">Brambleford</span>
        <span class="brand__sub">Landscape Construction</span>
      </span>
    </div>
  </section>

  <section class="card card--back" aria-label="Business card back">
    <svg class="waves" viewBox="0 0 525 300" preserveAspectRatio="none" aria-hidden="true">
      <path class="waves__stripe" d="M40 50 C110 120 200 160 320 162 C410 163 470 132 525 100 L525 112 C470 144 410 170 320 170 C210 168 120 128 40 54 Z" fill="#2a78d3"/>
      <path class="waves__green" d="M0 52 C80 140 190 176 300 176 C190 180 80 150 0 70 Z" fill="#a6d63a"/>
      <path class="waves__base" d="M0 70 C80 150 190 180 300 176 C390 173 460 150 525 122 L525 300 L0 300 Z" fill="#2a78d3"/>
    </svg>

    <div class="brand">
      <span class="brand__dot"></span>
      <span class="brand__name">
        <span class="brand__title">Brambleford</span>
        <span class="brand__sub">Landscape Construction</span>
      </span>
    </div>

    <div class="contact">
      <p class="contact__name">Dana Whitlow</p>
      <p class="contact__role">Director</p>
      <p class="contact__line">(877) 62Vista
        <svg class="contact__icon" viewBox="0 0 12 12" aria-hidden="true"><path d="M3 1 L5 3.5 L4 4.8 C4.6 6.2 5.8 7.4 7.2 8 L8.5 7 L11 9 L10 11 C5.5 11 1 6.5 1 2 Z" fill="#fff"/></svg>
      </p>
      <p class="contact__line">sales@bramblefordyards.example
        <svg class="contact__icon" viewBox="0 0 12 12" aria-hidden="true"><rect x="0.8" y="2.5" width="10.4" height="7" fill="none" stroke="#fff" stroke-width="1.2"/><path d="M1 3 L6 7 L11 3" fill="none" stroke="#fff" stroke-width="1.2"/></svg>
      </p>
      <p class="contact__line">www.bramblefordyards.example
        <svg class="contact__icon" viewBox="0 0 12 12" aria-hidden="true"><circle cx="6" cy="6" r="5" fill="none" stroke="#fff" stroke-width="1.1"/><ellipse cx="6" cy="6" rx="2.2" ry="5" fill="none" stroke="#fff" stroke-width="1"/><path d="M1 6 H11" stroke="#fff" stroke-width="1"/></svg>
      </p>
    </div>
  </section>

</body>
</html>
```